Tolbek cards

I want a simple business card that pops.
Logo on one side.
On side two i want.
"Are you thinking about a new building on your property, or renovating an existing structure? Contact".....
Owners Name: Dale Whitacre
Owners Phone number: 610-555-0187
Address:4076 Copper Ridge RD, Halloway, PA 17904
Committed to Quality, Service, and Integrity

```html
<!DOCTYPE html>
<html lang="en">
<head>
<meta charset="utf-8">
<title>Tolbek Builders LLC – Business Card</title>
<link rel="stylesheet" href="https://fonts.googleapis.com/css2?family=Archivo:wght@400;600;800&family=Kalam:wght@400&display=swap">
<style>
  :root {
    --backdrop: #2b2b2b;
    --brown-top: #9d8366;
    --brown-bottom: #553a28;
    --brown-dark: #4a3426;
    --brown-band-top: #9a8168;
    --brown-band-bottom: #6e5540;
    --paper: #f2f1ef;
    --ink: #3a2a20;
    --ink-soft: #5a4a40;
    --cream: #efebe6;
    --rule: #b9b3ad;
    --icon: #7a6a60;
  }
  * { box-sizing: border-box; margin: 0; padding: 0; }
  html, body {
    width: 1200px; height: 576px; overflow: hidden;
    background: var(--backdrop);
    font-family: "Archivo", Arial, sans-serif;
  }
  .canvas { position: relative; width: 1200px; height: 576px; }

  .card {
    position: absolute; width: 484px; height: 292px;
    border-radius: 10px; overflow: hidden;
  }

  /* Front side */
  .card--front {
    left: 102px; top: 139px;
    background: linear-gradient(180deg, var(--brown-top) 0%, var(--brown-bottom) 100%);
    color: var(--cream);
  }
  .brand { position: absolute; left: 0; right: 0; text-align: center; }
  .brand__mark { position: absolute; background: currentColor; }
  .card--front .brand { top: 0; height: 100%; }
  .card--front .brand__mark { left: 212px; top: 78px; width: 60px; height: 60px; }
  .brand__name, .brand__sub { display: block; font-weight: 800; line-height: 1; }
  .card--front .brand__name { position: absolute; left: 0; right: 0; top: 154px; font-size: 48px; letter-spacing: 1.5px; }
  .card--front .brand__sub { position: absolute; left: 0; right: 0; top: 201px; font-size: 16px; letter-spacing: 1.5px; }

  .tagline-front {
    position: absolute; left: 0; right: 0; top: 254px;
    display: flex; align-items: center; justify-content: center; gap: 10px;
    font-size: 13px; color: var(--cream);
  }
  .tagline-front .line { width: 68px; height: 1px; background: linear-gradient(90deg, transparent, var(--cream)); }
  .tagline-front .line--right { background: linear-gradient(90deg, var(--cream), transparent); }

  /* Back side */
  .card--back { left: 596px; top: 138px; background: var(--paper); color: var(--ink); }
  .pitch {
    position: absolute; left: 0; right: 0; top: 24px;
    text-align: center; font-family: "Kalam", "Comic Sans MS", cursive;
    font-size: 17.5px; line-height: 22px; color: var(--ink);
  }
  .card--back .brand { left: 36px; width: 200px; top: 0; height: 100%; color: var(--brown-dark); }
  .card--back .brand__mark { left: 78px; top: 104px; width: 44px; height: 44px; }
  .card--back .brand__name { position: absolute; left: 0; right: 0; top: 172px; font-size: 36px; letter-spacing: 0.5px; }
  .card--back .brand__sub { position: absolute; left: 0; right: 0; top: 208px; font-size: 13px; letter-spacing: 1.2px; }

  .contact { position: absolute; left: 258px; top: 109px; width: 176px; }
  .contact__label { font-size: 9px; color: var(--ink-soft); padding-bottom: 2px; border-bottom: 1px solid var(--rule); }
  .contact__name { font-size: 19px; font-weight: 800; color: var(--ink); margin-top: 6px; letter-spacing: 0.3px; white-space: nowrap; }
  .contact__row { display: flex; gap: 6px; font-size: 12.5px; color: var(--ink); margin-top: 6px; line-height: 15px; }
  .contact__row svg { flex: none; width: 12px; height: 12px; margin-top: 2px; }

  .tagline-back {
    position: absolute; left: 0; right: 0; bottom: 0; height: 30px;
    background: linear-gradient(180deg, var(--brown-band-top), var(--brown-band-bottom));
    color: var(--cream); font-size: 13px;
    display: flex; align-items: center; justify-content: center;
  }
</style>
</head>
<body>
<main class="canvas">

  <section class="card card--front" aria-label="Card front">
    <div class="brand">
      <span class="brand__mark" aria-hidden="true"></span>
      <span class="brand__name">TOLBEK</span>
      <span class="brand__sub">BUILDERS LLC</span>
    </div>
    <p class="tagline-front">
      <span class="line"></span>
      <span>Committed to Quality, Service &amp; Integrity</span>
      <span class="line line--right"></span>
    </p>
  </section>

  <section class="card card--back" aria-label="Card back">
    <p class="pitch">Are you thinking about a new building on your<br>property, or renovating an existing structure?</p>

    <div class="brand">
      <span class="brand__mark" aria-hidden="true"></span>
      <span class="brand__name">TOLBEK</span>
      <span class="brand__sub">BUILDERS LLC</span>
    </div>

    <div class="contact">
      <p class="contact__label">Contact:</p>
      <p class="contact__name">DALE WHITACRE</p>
      <p class="contact__row">
        <svg viewBox="0 0 12 12" aria-hidden="true"><circle cx="6" cy="6" r="5.3" fill="none" stroke="var(--icon)" stroke-width="1"/><path d="M4 3.2l1 1.3-.6.8c.5 1 1.2 1.7 2.2 2.2l.8-.6 1.3 1-.6 1c-2.6-.4-4.3-2.1-4.7-4.7z" fill="var(--icon)"/></svg>
        <span>610-555-0187</span>
      </p>
      <p class="contact__row">
        <svg viewBox="0 0 12 12" aria-hidden="true"><path d="M6 11.3S2.2 7.3 2.2 4.6a3.8 3.8 0 017.6 0C9.8 7.3 6 11.3 6 11.3z" fill="none" stroke="var(--icon)" stroke-width="1"/><circle cx="6" cy="4.6" r="1.3" fill="var(--icon)"/></svg>
        <span>4076 Copper Ridge RD,<br>Halloway, PA 17904</span>
      </p>
    </div>

    <p class="tagline-back">Committed to Quality, Service &amp; Integrity</p>
  </section>

</main>
</body>
</html>
```